Business Card Re-Design/Update

We'd like to update out business cards. I've included our current "Style guide" which has the colour scheme of the organisation in it. I've also included the branding files with logos etc in them.

I've also included a copy of one of our existing cards so that you can see how ugly/dated they look. I'd like a fresh modern corporate look.

Target Market(s)

These are for our clients, potential clients, industry contacts - like all business cards

Contact Information for Business Card

Name
Position
Company Address - Level 1, 47 Fernby Street, Carlow Qld 4072
Direct Phone
mobile
Email
Website -www.korvalit.com.au
Logo

Colors

Designer to choose colors to be used in the design.

Requirements
Must have
• Main Logo
• Cards will need to be editable to be able to personalize them for each new employee.
Nice to have
• The MapOut, ShipWell, KeepSteady would be okay to have if they can be sensibly and professionally added to the look without detracting from the main imagery.
• Maybe they could go on the back of the card? will leave this to your creative discretion as to whether/where they fit.
Should not have
• Should not have decorative or script fonts

```html
<!DOCTYPE html>
<html lang="en">
<head>
<meta charset="utf-8">
<title>korvalIT business card</title>
<link rel="stylesheet" href="https://fonts.googleapis.com/css2?family=Roboto:wght@400;500;700&family=Roboto+Condensed:wght@400;500&display=swap">
<style>
  :root {
    --stage: #1f1f1f;
    --paper: #f3f3f3;
    --brand-red: #c4161c;
    --brand-red-dark: #a81218;
    --ink: #262626;
    --ink-soft: #555555;
    --rule: #3a3a3a;
    --white: #ffffff;
  }
  html, body {
    margin: 0;
    padding: 0;
    width: 1200px;
    height: 960px;
    overflow: hidden;
    background: var(--stage);
  }
  .canvas {
    position: relative;
    width: 1200px;
    height: 960px;
    background: var(--stage);
    font-family: "Roboto", Arial, sans-serif;
  }
  .card {
    position: absolute;
    width: 600px;
    height: 342px;
    overflow: hidden;
    box-shadow: 0 4px 14px rgba(0,0,0,0.5);
  }
  /* Front */
  .card-front {
    left: 322px;
    top: 108px;
    background: var(--paper);
  }
  .brand {
    position: absolute;
    right: 34px;
    top: 42px;
    display: flex;
    align-items: center;
    gap: 12px;
  }
  .brand-mark {
    width: 30px;
    height: 30px;
    background: var(--brand-red);
  }
  .brand-name {
    font-family: "Roboto", Arial, sans-serif;
    font-weight: 500;
    font-size: 36px;
    letter-spacing: -0.5px;
    color: var(--ink);
    line-height: 1;
  }
  .person {
    position: absolute;
    left: 36px;
    top: 142px;
  }
  .person-name {
    margin: 0;
    font-family: "Roboto Condensed", Arial, sans-serif;
    font-weight: 500;
    font-size: 21px;
    color: var(--brand-red);
    line-height: 1.1;
  }
  .person-role {
    margin: 3px 0 0;
    font-family: "Roboto Condensed", Arial, sans-serif;
    font-size: 15px;
    color: var(--ink);
  }
  .divider {
    position: absolute;
    left: 36px;
    right: 34px;
    top: 195px;
    height: 1px;
    background: var(--rule);
  }
  .contacts {
    position: absolute;
    left: 36px;
    top: 207px;
    margin: 0;
    padding: 0;
    list-style: none;
  }
  .contacts li {
    display: flex;
    align-items: center;
    height: 19.3px;
    font-size: 14px;
    color: var(--ink-soft);
  }
  .contacts svg {
    width: 13px;
    height: 13px;
    margin-right: 9px;
    fill: var(--brand-red);
  }
  .address {
    position: absolute;
    right: 34px;
    top: 265px;
    margin: 0;
    text-align: right;
    font-style: normal;
    font-size: 14px;
    line-height: 19.3px;
    color: var(--ink-soft);
  }
  .footer-bands {
    position: absolute;
    left: 0;
    bottom: 0;
    width: 600px;
    height: 30px;
  }
  .web {
    position: absolute;
    right: 30px;
    bottom: 6px;
    font-size: 13px;
    letter-spacing: 1.6px;
    color: var(--white);
  }
  /* Back */
  .card-back {
    left: 320px;
    top: 493px;
    background: radial-gradient(ellipse at 50% 45%, #d91b21 0%, var(--brand-red) 55%, var(--brand-red-dark) 100%);
  }
  .back-brand {
    position: absolute;
    left: 0;
    right: 0;
    top: 112px;
    display: flex;
    justify-content: center;
    align-items: center;
    gap: 16px;
  }
  .back-brand .brand-mark {
    width: 44px;
    height: 44px;
    background: var(--white);
  }
  .back-brand .brand-name {
    font-size: 58px;
    font-weight: 700;
    color: var(--white);
  }
  .services {
    position: absolute;
    left: 46px;
    top: 276px;
    margin: 0;
    padding: 0;
    list-style: none;
    display: flex;
    gap: 34px;
  }
  .services li {
    display: flex;
    align-items: center;
    gap: 8px;
    font-weight: 500;
    font-size: 26px;
    letter-spacing: -0.4px;
    color: var(--white);
  }
  .services .service-mark {
    width: 16px;
    height: 16px;
    border: 3px solid var(--white);
    box-sizing: border-box;
  }
</style>
</head>
<body>
<main class="canvas">

  <section class="card card-front" aria-label="Business card front">
    <div class="brand">
      <span class="brand-mark" aria-hidden="true"></span>
      <span class="brand-name">korvalIT</span>
    </div>

    <div class="person">
      <h1 class="person-name">MARA THORNE</h1>
      <p class="person-role">Business Development Manager</p>
    </div>

    <div class="divider"></div>

    <ul class="contacts">
      <li><svg viewBox="0 0 24 24" aria-hidden="true"><path d="M6.6 10.8a15.1 15.1 0 0 0 6.6 6.6l2.2-2.2c.3-.3.7-.4 1-.2 1.1.4 2.3.6 3.6.6.6 0 1 .4 1 1V20c0 .6-.4 1-1 1A17 17 0 0 1 3 4c0-.6.4-1 1-1h3.5c.6 0 1 .4 1 1 0 1.3.2 2.5.6 3.6.1.3 0 .7-.2 1z"/></svg>+61 (0)7 3108 4452</li>
      <li><svg viewBox="0 0 24 24" aria-hidden="true"><path d="M6.6 10.8a15.1 15.1 0 0 0 6.6 6.6l2.2-2.2c.3-.3.7-.4 1-.2 1.1.4 2.3.6 3.6.6.6 0 1 .4 1 1V20c0 .6-.4 1-1 1A17 17 0 0 1 3 4c0-.6.4-1 1-1h3.5c.6 0 1 .4 1 1 0 1.3.2 2.5.6 3.6.1.3 0 .7-.2 1z"/></svg>+61 (0)7 3108 4467</li>
      <li><svg viewBox="0 0 24 24" aria-hidden="true"><path d="M7 1h10a2 2 0 0 1 2 2v18a2 2 0 0 1-2 2H7a2 2 0 0 1-2-2V3a2 2 0 0 1 2-2zm0 3v14h10V4zm5 15.2a1.2 1.2 0 1 0 0 2.4 1.2 1.2 0 0 0 0-2.4z"/></svg>+61 (0)412 560 238</li>
      <li><svg viewBox="0 0 24 24" aria-hidden="true"><path d="M6 2h12v6H6zM3 9h18a2 2 0 0 1 2 2v7h-4v4H5v-4H1v-7a2 2 0 0 1 2-2zm4 8v3h10v-3z"/></svg>+61 (0)7 3108 4490</li>
      <li><svg viewBox="0 0 24 24" aria-hidden="true"><path d="M2 5h20v2l-10 6L2 7zm0 4.3 10 6 10-6V19H2z"/></svg>mthorne@korvalit.com.au</li>
    </ul>

    <address class="address">22/58 Tarrow Park Road<br>Kelby QLD 4010</address>

    <svg class="footer-bands" viewBox="0 0 600 30" aria-hidden="true">
      <polygon points="0,8 345,8 331,22 0,22" fill="#222222"/>
      <polygon points="0,22 600,22 600,30 0,30" fill="#c4161c"/>
      <polygon points="352,2 600,2 600,30 326,30" fill="#c4161c"/>
    </svg>
    <span class="web">www.korvalit.com.au</span>
  </section>

  <section class="card card-back" aria-label="Business card back">
    <div class="back-brand">
      <span class="brand-mark" aria-hidden="true"></span>
      <span class="brand-name">korvalIT</span>
    </div>
    <ul class="services">
      <li><span class="service-mark" aria-hidden="true"></span>MapOut</li>
      <li><span class="service-mark" aria-hidden="true"></span>ShipWell</li>
      <li><span class="service-mark" aria-hidden="true"></span>KeepSteady</li>
    </ul>
  </section>

</main>
</body>
</html>
```